Venture Capital Firm Needs Website Redesign

We need a bold revamp of our website (https://halverine.vc/)
which at the moment looks washed out. We want a crisp, fresh and unique look. Feel free to keep as much or as little content in the site. The only thing we need to keep is a team section. The site should convey a clear distinction between our 3 product lines: Venture Capital, Private Credit, and Crypto. Two versions of our logo are attached and they should not change. For design inspirations, we like http://www.9plm.com/ for a more simple site and for a more built out site we like http://bluetorch.com/

Updates
Industry/Entity Type
Investment
Coding
Coded - Design and coding required
Number of Pages Required
1 page
Font styles to use
Colors
Designer to choose colors to be used in the design.
Requirements
Must have
- - Clear distinction between our 3 product lines: Venture Capital, Private Credit
- - Team section

Nice to have
- Some really creative aspect like http://www.9plm.com/ has with the distinction between first, second, and third kind

```html
<!DOCTYPE html>
<html lang="en">
<head>
<meta charset="utf-8">
<title>Halverine</title>
<link href="https://fonts.googleapis.com/css2?family=Montserrat:wght@500;600;700&family=Open+Sans:wght@400;600&display=swap" rel="stylesheet">
<style>
:root{
  --green:#8a9e2a;
  --green-dark:#6f8220;
  --forest:#1e4633;
  --forest-deep:#143426;
  --ink:#1b1b1b;
  --text:#555;
  --muted:#8a8a8a;
  --line:#d9d9d9;
  --grey-band:#e6e4e1;
  --navy:#16365f;
  --navy-deep:#0f2747;
  --sky:#4aa3d8;
  --mint:#3fb98a;
  --white:#fff;
}
*{box-sizing:border-box;margin:0;padding:0}
html,body{width:1200px;height:4712px;overflow:hidden}
body{position:relative;background:var(--white);font-family:"Open Sans",Arial,sans-serif;color:var(--text)}
.abs{position:absolute}
h1,h2,h3,.nav,.btn,.tag,.brand{font-family:"Montserrat",Arial,sans-serif}

/* nav */
.site-nav{left:0;top:0;width:1200px;height:98px;background:var(--white);z-index:5}
.brand{position:absolute;left:100px;top:36px;font-size:27px;font-weight:600;letter-spacing:1px;color:var(--forest)}
.nav{position:absolute;top:50px;font-size:12px;font-weight:600;color:#333}
.nav.active{color:var(--green)}

/* hero */
.hero{left:0;top:98px;width:1200px;height:580px;background:linear-gradient(135deg,#2d5d43,var(--forest) 55%,var(--forest-deep));clip-path:polygon(0 0,100% 0,100% 82%,0 100%)}
.hero-edge{left:0;top:98px;width:1200px;height:590px;background:var(--green);clip-path:polygon(0 96%,100% 80%,100% 82%,0 100%)}
.hero h1{position:absolute;left:0;top:226px;width:1200px;text-align:center;font-size:37px;font-weight:600;line-height:50px;color:var(--white)}
.btn{display:inline-block;background:var(--green);color:var(--white);font-size:13px;font-weight:600;border-radius:24px;text-align:center}
.hero .btn{position:absolute;left:519px;top:360px;width:162px;height:48px;line-height:48px}
.chev{width:40px;height:40px;border-radius:50%;background:var(--white);box-shadow:0 1px 4px rgba(0,0,0,.25);z-index:3}
.chev svg{position:absolute;left:12px;top:12px}

/* sections */
h2{font-size:33px;font-weight:700;color:var(--ink);letter-spacing:.5px}
.copy{font-size:14px;line-height:25px;color:var(--text)}
.logo-box{height:86px;border:1px solid var(--line);display:flex;align-items:center;justify-content:center;font-size:17px;font-weight:600;color:#4a4a4a}
.illus-card{border-radius:46px;transform:rotate(-14deg)}

/* about */
.about-band{left:0;top:2060px;width:1200px;height:630px;background:var(--grey-band);clip-path:polygon(0 0,100% 14%,100% 100%,0 86%)}
.rule{width:60px;height:3px;background:var(--green)}

/* team */
.team-card{top:2867px;width:328px;height:368px;background:var(--white);box-shadow:0 2px 10px rgba(0,0,0,.18)}
.photo{position:absolute;left:6px;top:6px;width:316px;height:206px;background:linear-gradient(180deg,#d9d9d9,#a9a9a9)}
.tag{position:absolute;left:6px;top:182px;width:136px;height:38px;line-height:38px;background:var(--green);color:var(--white);font-size:15px;font-weight:600;text-align:center}
.member{position:absolute;left:28px;top:236px;font-size:17px;font-weight:700;color:var(--ink);font-family:"Montserrat",sans-serif}
.role{position:absolute;left:28px;top:262px;font-size:12px;font-style:italic;color:var(--green)}
.bio{position:absolute;left:28px;top:286px;width:278px;font-size:12px;line-height:18px;color:var(--text)}
.socials{position:absolute;right:28px;top:240px;display:flex;gap:10px}
.socials span{width:12px;height:12px;background:#333}
.arrow-btn{width:34px;height:34px;border-radius:50%;border:1px solid #bbb;background:var(--white)}
.arrow-btn svg{position:absolute;left:11px;top:10px}

/* blog */
.blog{left:0;top:3330px;width:1200px;height:690px;background:linear-gradient(180deg,var(--navy) 0%,#1f4b7e 45%,var(--navy-deep) 100%);clip-path:polygon(0 0,100% 12%,100% 100%,0 88%)}
.blog-title{left:0;top:3470px;width:1200px;text-align:center;font-size:40px;font-weight:700;color:var(--white)}
.blog-sub{left:0;top:3522px;width:1200px;text-align:center;font-size:14px;color:#dfe8f2}
.post-head{left:97px;top:3649px;width:481px;height:46px;line-height:46px;background:var(--green);color:var(--white);font-size:17px;font-weight:600;padding-left:22px}
.post-body{left:97px;top:3705px;width:688px;height:163px;background:rgba(30,30,30,.88);padding:26px 24px;font-size:12.5px;line-height:22px;color:#eee}
.post-meta{margin-top:8px;font-size:11px;color:var(--green)}

/* contact */
.field{height:44px;border:1px solid #cfcfcf;padding:12px 22px;font-size:13px;color:#888}
.icon-circle{width:48px;height:48px;border-radius:50%;background:var(--green)}
.icon-circle svg{position:absolute;left:14px;top:13px}
.submit{left:841px;top:4522px;width:120px;height:44px;line-height:44px;background:#222;color:var(--white);font-size:14px;font-weight:600;text-align:center;font-family:"Montserrat",sans-serif}
.footer{left:0;top:4664px;width:1200px;text-align:center;font-size:11px;color:#444}
</style>
</head>
<body>

<header class="abs site-nav">
  <div class="brand">HALVERINE</div>
  <a class="nav active" style="left:408px">VENTURE</a>
  <a class="nav" style="left:522px">PRIVATE CREDIT</a>
  <a class="nav" style="left:680px">CRYPTO</a>
  <a class="nav" style="left:788px">ABOUT US</a>
  <a class="nav" style="left:908px">TEAM</a>
  <a class="nav" style="left:998px">BLOG</a>
  <svg class="abs" style="left:1088px;top:50px" width="14" height="14" viewBox="0 0 14 14"><circle cx="6" cy="6" r="4.5" fill="none" stroke="#8a9e2a" stroke-width="2"/><line x1="9.5" y1="9.5" x2="13" y2="13" stroke="#8a9e2a" stroke-width="2"/></svg>
</header>

<div class="abs hero-edge"></div>
<section class="abs hero">
  <div class="abs" style="left:550px;top:112px;width:100px;height:100px;border:3px solid #fff;border-radius:50%"></div>
  <h1>Halverine operates at the intersection<br>of technology &amp; novel asset classes</h1>
  <a class="btn">GET STARTED</a>
</section>
<div class="abs chev" style="left:580px;top:610px"><svg width="16" height="16" viewBox="0 0 16 16"><path d="M3 6l5 5 5-5" fill="none" stroke="#333" stroke-width="2"/></svg></div>

<!-- Venture capital -->
<section>
  <h2 class="abs" style="left:97px;top:765px">VENTURE CAPITAL</h2>
  <p class="abs copy" style="left:97px;top:818px;width:650px">We invest in early-stage startups led by founders who are passionate and knowledgeable about the markets they serve. We have our own software developers and product managers. We work with the founders in our portfolio to help them bring products to market, earning equity for this work and for the cash we invest in their companies.</p>
  <div class="abs logo-box" style="left:97px;top:960px;width:170px">Ridgeway Group</div>
  <div class="abs logo-box" style="left:280px;top:960px;width:166px">loopnote</div>
  <div class="abs logo-box" style="left:458px;top:960px;width:167px">tinyroam</div>
  <div class="abs logo-box" style="left:638px;top:960px;width:166px">Corelane</div>
  <div class="abs illus-card" role="img" aria-label="Illustration of a hand holding a growing coin plant" style="left:835px;top:720px;width:360px;height:360px;background:linear-gradient(135deg,#6fc0ea,var(--sky))"></div>
</section>

<!-- Private credit -->
<section>
  <div class="abs illus-card" role="img" aria-label="Illustration of a hand holding a credit score report" style="left:-40px;top:1150px;width:400px;height:370px;background:linear-gradient(135deg,#62d0a3,var(--mint))"></div>
  <h2 class="abs" style="left:427px;top:1207px">PRIVATE CREDIT</h2>
  <p class="abs copy" style="left:427px;top:1254px;width:650px">Halverine Private Credit provides capital to lending businesses that are focused on using technology to establish new credit markets, create new credit products or dramatically re-invent an existing form of credit. We believe that the pioneers who build something truly different in a credit market will create the most sustainable business models. Given our heritage as a venture firm, we are comfortable with emerging businesses and can provide capital for a company's first loan.</p>
  <div class="abs logo-box" style="left:427px;top:1430px;width:167px">Brisa Lending</div>
  <div class="abs logo-box" style="left:606px;top:1430px;width:167px" role="img" aria-label="Partner badge"><span style="width:40px;height:40px;border-radius:50%;background:#9aa66a"></span></div>
  <div class="abs logo-box" style="left:785px;top:1430px;width:170px">Tallyfold</div>
</section>

<!-- Crypto -->
<section>
  <div class="abs illus-card" role="img" aria-label="Soft green backdrop shape" style="left:820px;top:1620px;width:400px;height:230px;background:linear-gradient(135deg,#b6d45b,#9bbf3a)"></div>
  <h2 class="abs" style="left:97px;top:1677px">CRYPTO</h2>
  <p class="abs copy" style="left:97px;top:1723px;width:580px">The Halverine Crypto Index tracks the top 15 cryptocurrencies weighted by market cap and rebalanced twice a month. We believe this is the simplest and most cost-effective way to obtain cryptocurrency exposure. Our process has been designed by experts from financial services and cryptocurrency industries.</p>
  <a class="abs btn" style="left:97px;top:1862px;width:136px;height:40px;line-height:40px;font-size:12px">LEARN MORE</a>
  <div class="abs" style="left:532px;top:1846px;width:104px;height:104px;border:3px solid #222;border-radius:50%"></div>
  <div class="abs" role="img" aria-label="Desktop monitor showing a crypto index line chart" style="left:763px;top:1737px;width:337px;height:273px;background:linear-gradient(180deg,#3a3a3a 0,#3a3a3a 72%,#bdbdbd 72%,#e3e3e3 100%);border-radius:6px"></div>
</section>
<div class="abs chev" style="left:580px;top:2084px"><svg width="16" height="16" viewBox="0 0 16 16"><path d="M3 11l5-5 5 5" fill="none" stroke="#333" stroke-width="2"/></svg></div>

<!-- About -->
<div class="abs about-band"></div>
<section>
  <h2 class="abs" style="left:103px;top:2252px">ABOUT US</h2>
  <div class="abs rule" style="left:103px;top:2302px"></div>
  <p class="abs copy" style="left:103px;top:2330px;width:600px;line-height:29px">Halverine operates three businesses that bridge technology and finance. We invest in pre-seed venture capital, and build software for the companies we invest in. We manage direct private credit funds that provide private credit capital to alternative private credit platforms, enabling them to finance the loans they originate. We create crypto funds for individuals, RIAs and institutions to get simple and easy access to cryptocurrencies.</p>
  <div class="abs" style="left:757px;top:2267px;width:252px;height:252px;border:6px solid #222;border-radius:50%"></div>
  <div class="abs" style="left:757px;top:2378px;width:252px;text-align:center;font-family:'Montserrat',sans-serif;font-size:24px;font-weight:600;color:#222;letter-spacing:2px">HALVERINE</div>
</section>

<!-- Team -->
<section>
  <h2 class="abs" style="left:0;top:2740px;width:1200px;text-align:center;font-size:40px">OUR TEAM</h2>
  <p class="abs" style="left:0;top:2792px;width:1200px;text-align:center;font-size:13px">The very best helping the very best.</p>
  <div class="abs rule" style="left:585px;top:2826px;width:30px;height:2px;background:#888"></div>

  <div class="abs arrow-btn" style="left:40px;top:3038px"><svg width="12" height="12" viewBox="0 0 12 12"><path d="M8 2L4 6l4 4" fill="none" stroke="#555" stroke-width="1.6"/></svg></div>
  <div class="abs arrow-btn" style="left:1124px;top:3038px"><svg width="12" height="12" viewBox="0 0 12 12"><path d="M4 2l4 4-4 4" fill="none" stroke="#555" stroke-width="1.6"/></svg></div>

  <article class="abs team-card" style="left:97px">
    <div class="photo" role="img" aria-label="Portrait photo of Omar Vessel"></div>
    <div class="tag">PARTNER</div>
    <div class="member">OMAR VESSEL</div><div class="socials"><span></span><span></span></div>
    <div class="role">PARTNER</div>
    <p class="bio">Omar is a Partner for Halverine VC Fund. He is also a cofounder of Halverine.</p>
  </article>
  <article class="abs team-card" style="left:440px">
    <div class="photo" role="img" aria-label="Portrait photo of Rohan Iyerwal"></div>
    <div class="tag">PARTNER</div>
    <div class="member">ROHAN IYERWAL</div><div class="socials"><span></span><span></span></div>
    <div class="role">PARTNER</div>
    <p class="bio">Rohan is a Partner for Halverine Crypto. He previously invested at Quillmere Capital and Ostenbrook Ventures.</p>
  </article>
  <article class="abs team-card" style="left:779px">
    <div class="photo" role="img" aria-label="Portrait photo of Tariq Selbourne"></div>
    <div class="tag">PARTNER</div>
    <div class="member">TARIQ SELBOURNE</div><div class="socials"><span></span><span></span></div>
    <div class="role">PARTNER</div>
    <p class="bio">Tariq is a Partner for Halverine VC Fund. He is also a cofounder of Halverine and Signal Crew.</p>
  </article>
</section>

<!-- Blog -->
<div class="abs blog" role="img" aria-label="Deep blue ocean scene with an iceberg below the waterline"></div>
<div class="abs chev" style="left:580px;top:3356px"><svg width="16" height="16" viewBox="0 0 16 16"><path d="M3 11l5-5 5 5" fill="none" stroke="#333" stroke-width="2"/></svg></div>
<h2 class="abs blog-title">OUR BLOG</h2>
<p class="abs blog-sub">Nam libero tempore, cum soluta nobis est eligen</p>
<div class="abs post-head">HOW TO BUILD A “WOW” USER EXPERIENCE</div>
<div class="abs post-body">
  You must have thought that software development is the most complex part in rolling out a successful product. Sure, it's a nightmare for many, but building a solid user experience is even challenging. And yes, user experience design is NOT software development...<span style="float:right;color:var(--green)">[Read More]</span>
  <div class="post-meta">By Admin &nbsp;|&nbsp; Comments</div>
</div>
<svg class="abs" style="left:918px;top:3776px" width="14" height="20" viewBox="0 0 14 20"><path d="M11 2L3 10l8 8" fill="none" stroke="#fff" stroke-width="2.5"/></svg>
<svg class="abs" style="left:952px;top:3776px" width="14" height="20" viewBox="0 0 14 20"><path d="M3 2l8 8-8 8" fill="none" stroke="#fff" stroke-width="2.5"/></svg>

<!-- Contact -->
<section>
  <h2 class="abs" style="left:0;top:4078px;width:1200px;text-align:center;font-size:40px">CONTACT US</h2>
  <p class="abs" style="left:0;top:4130px;width:1200px;text-align:center;font-size:13px">We would love to hear from you.</p>
  <div class="abs icon-circle" style="left:362px;top:4212px"><svg width="20" height="22" viewBox="0 0 20 22"><path d="M10 1a7 7 0 0 0-7 7c0 5 7 13 7 13s7-8 7-13a7 7 0 0 0-7-7z" fill="#fff"/><circle cx="10" cy="8" r="2.6" fill="#8a9e2a"/></svg></div>
  <p class="abs" style="left:430px;top:4214px;font-size:12.5px;line-height:20px;color:#333">218 Orchard Row, Suite 410<br>Harborview, HV 20418</p>
  <div class="abs icon-circle" style="left:645px;top:4212px"><svg width="20" height="22" viewBox="0 0 20 22"><rect x="1" y="5" width="18" height="13" fill="#fff"/><path d="M1 5l9 7 9-7" fill="none" stroke="#8a9e2a" stroke-width="1.6"/></svg></div>
  <p class="abs" style="left:713px;top:4214px;font-size:12.5px;line-height:20px;color:#333">Email Us :<br>hello@halverine.vc</p>

  <div class="abs field" style="left:239px;top:4292px;width:354px">Enter Name</div>
  <div class="abs field" style="left:606px;top:4292px;width:355px">Enter Email</div>
  <div class="abs field" style="left:239px;top:4348px;width:354px">Phone</div>
  <div class="abs field" style="left:606px;top:4348px;width:355px">Address</div>
  <div class="abs field" style="left:239px;top:4404px;width:722px;height:106px">Message</div>
  <div class="abs submit">SUBMIT</div>
</section>

<div class="abs" style="left:60px;top:4634px;width:1080px;height:1px;background:#e2e2e2"></div>
<p class="abs footer">Copyright © 2018 Halverine.All right reserved &nbsp;|&nbsp; Privacy policy &nbsp;|&nbsp; Terms and Use</p>

</body>
</html>
```